Business card design Needed for new logo / Construction business, home extensions and new builds

We need a business card design using our new logo files which i will attach to this project :)

We are a small construction business specialising in home extensions, new builds and property development. We are very ambitious and would appreciate professional and elegant designs for our new business card.

Very serious about using the services on MakerQuarry and recently acquired our new logo from here :)

Please get involved, i will feedback when i can as i am very busy but can respond daily, thanks

Target Market(s)

People that want to build onto their houses, new building developments or adding too their existing property

Industry/Entity Type

Construction

Contact Information for Business Card

Renwick Tolliver Construction, Lionel Ashby (Managing Director), Tel 07822254961, email - info@renwick-tolliver, www.renwick-tolliver.co.uk

Colors

Designer to choose colors to be used in the design.

Requirements
Must have
• I like a deep grey on the back please. A lot of you have provided black from and back, try mixing things up a little. The black looks cool 😎 Thanks

```html
<!DOCTYPE html>
<html lang="en">
<head>
<meta charset="utf-8">
<title>Renwick Tolliver Construction – Business Card</title>
<link href="https://fonts.googleapis.com/css2?family=Cinzel:wght@500&family=EB+Garamond:wght@400;500&display=swap" rel="stylesheet">
<style>
  :root {
    --backdrop: #c9c9c9;
    --card-black: #151515;
    --grey-light: #4a4a4a;
    --grey: #363636;
    --grey-deep: #262626;
    --gold: #d9a534;
    --silver: #e4e4e4;
    --silver-dim: #bdbdbd;
    --divider: #3a3a3a;
  }
  * { margin: 0; padding: 0; box-sizing: border-box; }
  html, body { width: 1200px; height: 800px; overflow: hidden; }
  body {
    background: var(--backdrop);
    display: flex;
    align-items: center;
    justify-content: center;
    gap: 60px;
    font-family: "EB Garamond", Georgia, serif;
  }
  .card {
    width: 520px;
    height: 300px;
    position: relative;
    border-bottom: 2px solid var(--gold);
    box-shadow: 0 10px 24px rgba(0,0,0,.25);
    overflow: hidden;
  }
  .card-front {
    background: var(--card-black);
    display: flex;
  }
  .brand-panel {
    width: 50%;
    display: flex;
    flex-direction: column;
    align-items: center;
    justify-content: center;
    gap: 16px;
    text-align: center;
    padding-top: 20px;
  }
  .brand-square {
    width: 40px;
    height: 40px;
    background: var(--gold);
  }
  .brand-name {
    font-family: "Cinzel", Georgia, serif;
    font-weight: 500;
    color: var(--silver);
    font-size: 21px;
    line-height: 1.25;
    letter-spacing: 1px;
  }
  .brand-name .brand-sub { display: block; font-size: 15px; letter-spacing: 2px; }
  .panel-divider {
    width: 1px;
    background: var(--divider);
    margin: 60px 0 40px;
  }
  .contact-panel {
    flex: 1;
    padding: 50px 0 0 28px;
    color: var(--silver);
  }
  .person-name {
    font-family: "Cinzel", Georgia, serif;
    font-weight: 500;
    font-size: 20px;
    letter-spacing: 1px;
  }
  .person-role {
    color: var(--gold);
    font-size: 15px;
    margin-bottom: 14px;
  }
  .contact-list { list-style: none; font-size: 14px; line-height: 1.55; }
  .contact-list li { display: flex; align-items: center; gap: 8px; }
  .contact-list svg { width: 12px; height: 12px; fill: var(--silver-dim); flex: none; }
  .address { margin-top: 16px; font-size: 14px; line-height: 1.45; color: var(--silver-dim); }
  .card-back {
    display: flex;
    align-items: center;
    justify-content: center;
  }
  .back-texture {
    position: absolute;
    inset: 0;
    background: linear-gradient(135deg, var(--grey-light) 0%, var(--grey) 50%, var(--grey-deep) 100%);
  }
  .back-brand {
    position: relative;
    display: flex;
    align-items: center;
    gap: 10px;
    font-family: "Cinzel", Georgia, serif;
    font-weight: 500;
    font-size: 17px;
    letter-spacing: 1px;
    color: var(--gold);
  }
  .back-square { width: 14px; height: 14px; background: var(--gold); }
</style>
</head>
<body>
  <section class="card card-front">
    <div class="brand-panel">
      <div class="brand-square"></div>
      <div class="brand-name">Renwick Tolliver<span class="brand-sub">Construction</span></div>
    </div>
    <div class="panel-divider"></div>
    <div class="contact-panel">
      <h1 class="person-name">LIONEL ASHBY</h1>
      <p class="person-role">Managing Director</p>
      <ul class="contact-list">
        <li><svg viewBox="0 0 24 24"><path d="M6.6 10.8a15 15 0 0 0 6.6 6.6l2.2-2.2c.3-.3.7-.4 1-.2 1.1.4 2.3.6 3.6.6.6 0 1 .4 1 1V20c0 .6-.4 1-1 1A17 17 0 0 1 3 4c0-.6.4-1 1-1h3.5c.6 0 1 .4 1 1 0 1.3.2 2.5.6 3.6.1.3 0 .7-.2 1z"/></svg>07822254961</li>
        <li><svg viewBox="0 0 24 24"><path d="M2 5h20v14H2zm2 2v.5l8 5 8-5V7l-8 5z"/></svg>info@renwick-tolliver</li>
        <li><svg viewBox="0 0 24 24"><path d="M12 2a10 10 0 1 0 0 20 10 10 0 0 0 0-20zm0 2c.8 1.2 1.5 2.5 1.9 4h-3.8c.4-1.5 1.1-2.8 1.9-4zM4.3 14a8 8 0 0 1 0-4h3.4a16 16 0 0 0 0 4zM12 20c-.8-1.2-1.5-2.5-1.9-4h3.8c-.4 1.5-1.1 2.8-1.9 4zm2.3-6H9.7a14 14 0 0 1 0-4h4.6a14 14 0 0 1 0 4zm2 0a16 16 0 0 0 0-4h3.4a8 8 0 0 1 0 4z"/></svg>www.renwick-tolliver.co.uk</li>
      </ul>
      <p class="address">421, Address line goes here<br>45452, Country Name</p>
    </div>
  </section>

  <section class="card card-back">
    <div class="back-texture" role="img" aria-label="Embossed repeating brand mark pattern on deep grey stock"></div>
    <div class="back-brand"><span class="back-square"></span>Renwick Tolliver</div>
  </section>
</body>
</html>
```